holloway paving service

Needs to have phone number 0418259730 and email markholloway@brightmail.com.au.
ABN 62318470915
name mark holloway

For all your concreting solutions
Excavation
Exposed & colour concrete
House & shed slabs
Driveways
Landing & steps

Contact Information for Business Card

ph 0418259730
email markholloway@brightmail.com.au.
ABN 62318470915
name mark holloway

```html
<!DOCTYPE html>
<html lang="en">
<head>
<meta charset="utf-8">
<title>Holloway Paving Service – Business Card</title>
<link rel="stylesheet" href="https://fonts.googleapis.com/css2?family=Open+Sans:wght@400;600;700&display=swap">
<style>
  :root {
    --orange: #f06a23;
    --grey: #666666;
    --white: #ffffff;
    --backdrop: #3a3a3a;
    --shadow: rgba(0, 0, 0, 0.45);
  }
  * { margin: 0; padding: 0; box-sizing: border-box; }
  html, body {
    width: 1200px;
    height: 802px;
    overflow: hidden;
    background: var(--backdrop);
    font-family: "Open Sans", Arial, sans-serif;
  }
  .sheet {
    position: relative;
    width: 1200px;
    height: 802px;
  }
  .card {
    position: absolute;
    top: 240px;
    width: 540px;
    height: 323px;
    box-shadow: 0 4px 10px var(--shadow);
    overflow: hidden;
  }
  /* Front */
  .card--front {
    left: 40px;
    background: var(--orange);
    color: var(--white);
  }
  .front__panel {
    position: absolute;
    left: 0; top: 0;
    width: 200px;
    height: 100%;
    background: var(--grey);
  }
  .front__brand {
    position: absolute;
    left: 28px;
    top: 112px;
    width: 160px;
    font-size: 24px;
    font-weight: 700;
    line-height: 1.2;
    text-transform: uppercase;
    color: var(--white);
  }
  .front__details {
    position: absolute;
    right: 32px;
    top: 32px;
    text-align: right;
  }
  .front__name {
    font-size: 19px;
    font-weight: 700;
    text-transform: uppercase;
    margin-bottom: 14px;
  }
  .front__line {
    font-size: 14px;
    line-height: 23px;
  }
  .front__services {
    position: absolute;
    right: 32px;
    top: 206px;
    text-align: right;
  }
  .front__tagline {
    font-size: 12px;
    line-height: 17px;
    text-transform: uppercase;
    margin-bottom: 6px;
  }
  .front__service-line {
    font-size: 14px;
    line-height: 19.5px;
  }
  /* Back */
  .card--back {
    left: 620px;
    background: var(--white);
  }
  .back__lockup {
    position: absolute;
    left: 80px;
    top: 110px;
    display: flex;
    align-items: center;
    height: 104px;
  }
  .back__square {
    width: 44px;
    height: 44px;
    background: var(--orange);
    margin-right: 20px;
  }
  .back__rule {
    width: 2px;
    height: 104px;
    background: var(--orange);
    margin-right: 12px;
  }
  .back__text {
    display: flex;
    flex-direction: column;
    align-items: center;
  }
  .back__brand {
    font-size: 21px;
    font-weight: 600;
    text-transform: uppercase;
    color: var(--orange);
    line-height: 1.1;
  }
  .back__phone {
    margin-top: 6px;
    font-size: 16px;
    letter-spacing: 2px;
    color: var(--orange);
  }
</style>
</head>
<body>
<main class="sheet">
  <section class="card card--front">
    <div class="front__panel"></div>
    <div class="front__brand">Holloway Paving Service</div>
    <div class="front__details">
      <p class="front__name">Mark Holloway</p>
      <p class="front__line">ABN 62318470915</p>
      <p class="front__line">markholloway@brightmail.com.au</p>
    </div>
    <div class="front__services">
      <p class="front__tagline">For all your concreting<br>solutions</p>
      <p class="front__service-line">Excavation &nbsp;|&nbsp;Landing &amp; steps</p>
      <p class="front__service-line">House &amp; shed slabs &nbsp;|&nbsp; Driveways</p>
      <p class="front__service-line">Exposed &amp; colour concrete</p>
    </div>
  </section>

  <section class="card card--back">
    <div class="back__lockup">
      <div class="back__square"></div>
      <div class="back__rule"></div>
      <div class="back__text">
        <p class="back__brand">Holloway Paving Service</p>
        <p class="back__phone">0418259730</p>
      </div>
    </div>
  </section>
</main>
</body>
</html>
```